Bright, Bold Sydney Tutoring Business Flyer Advertisment

Lumora is an up and coming tutoring business located on Sydney's Upper North Shore catering to school students of all ages. We need a flyer designed for notice boards and letter box drops to attract new clients. Our tutors are mostly university education students who are fresh, dedicated and passionate about their areas of teaching. The flyer should exhibit a bright, bold, modern, clean cut style which would appeal to both students and parents. I have attached our logo (the flyer could reflect this colour scheme), and a PDF which outlines the information we would like to appear on the flyer. This is not set in stone, but designed to act as an extremely loose guide for your creativity !

Target Market(s)

Affluent School Students and Parents

Industry/Entity Type

Tutoring

Requirements
Must have
• Logo, $10 offer, company description.
Nice to have
• Grabbing headlines to attract new clients, such as "Feeling overwhelmed at school?". We are looking for an eye catching, clean cut and professional design that has the colours to attract kids and the tone to attract parents.

```html
<!DOCTYPE html>
<html lang="en">
<head>
<meta charset="utf-8">
<title>Lumora Tutoring Flyer</title>
<link href="https://fonts.googleapis.com/css2?family=Roboto+Slab:wght@700&family=Questrial&display=swap" rel="stylesheet">
<style>
  :root {
    --page-bg: #e7e5ea;
    --paper: #ffffff;
    --ink: #3a3a3c;
    --banner: #2e2b2c;
    --pink: #f39ac0;
    --brain-pink: #f4a6c4;
    --sky: #4a9fd8;
    --white: #ffffff;
  }
  * { box-sizing: border-box; margin: 0; padding: 0; }
  html, body {
    width: 969px; height: 1200px; overflow: hidden;
    background: var(--page-bg);
  }
  .flyer {
    position: absolute; left: 0; top: 0;
    width: 624px; height: 865px;
    background: var(--paper);
    transform-origin: 0 0;
    transform: translate(79px, 37px) scale(1.3);
    overflow: hidden;
    font-family: "Questrial", "Century Gothic", sans-serif;
    color: var(--ink);
  }
  .hero {
    position: absolute; left: 0; top: 0; width: 624px; height: 413px;
    background:
      radial-gradient(ellipse 220px 260px at 470px 230px, rgba(120,140,190,.85), rgba(120,140,190,0) 70%),
      radial-gradient(ellipse 160px 120px at 250px 110px, rgba(205,140,80,.8), rgba(205,140,80,0) 75%),
      linear-gradient(180deg, #6d94b8 0%, #8aa5a8 35%, #b7a58a 60%, #d8d4cc 80%, #c9c9cd 100%);
  }
  .headlines {
    position: absolute; left: 38px; top: 82px;
    list-style: none;
  }
  .headline {
    border-left: 2px solid var(--pink);
    padding-left: 8px;
    margin-bottom: 20px;
    font-family: "Roboto Slab", Georgia, serif;
    font-weight: 700;
    font-size: 19px;
    line-height: 22px;
    color: var(--white);
    text-transform: uppercase;
    letter-spacing: .3px;
    text-shadow: 0 1px 3px rgba(0,0,0,.35);
  }
  .intro {
    position: absolute; left: 47px; top: 430px; width: 533px;
    font-size: 16.5px; line-height: 22px;
    text-align: justify;
  }
  .offer {
    position: absolute; left: 48px; top: 526px; width: 523px; height: 68px;
    background: var(--banner);
    text-align: center;
    padding-top: 4px;
    white-space: nowrap;
    text-transform: uppercase;
    font-size: 24px; line-height: 29px;
    letter-spacing: -.5px;
  }
  .offer-lead { color: var(--white); display: block; }
  .offer-deal { color: var(--pink); display: block; }
  .call-to-action {
    position: absolute; left: 0; top: 602px; width: 624px;
    text-align: center; text-transform: uppercase;
    font-size: 10.5px; color: #222;
  }
  .brand {
    position: absolute; left: 0; top: 640px; width: 624px; height: 160px;
    display: flex; align-items: center; justify-content: center; gap: 14px;
  }
  .brand-mark {
    width: 46px; height: 46px; border-radius: 50%;
    background: var(--sky);
  }
  .brand-name {
    font-size: 48px; color: #2a2a2a; letter-spacing: .5px;
  }
  .contact-bar {
    position: absolute; left: 0; top: 809px; width: 624px; height: 56px;
    background: var(--sky);
    color: var(--white);
    text-align: center;
  }
  .contact-row {
    display: flex; justify-content: center; align-items: center; gap: 6px;
  }
  .contact-row.primary { font-size: 16px; padding-top: 6px; gap: 6px; }
  .contact-row.primary .gap { width: 12px; }
  .contact-row.address { font-size: 12.5px; padding-top: 3px; }
  .icon { width: 14px; height: 14px; flex: none; }
  .icon.small { width: 11px; height: 11px; }
</style>
</head>
<body>
  <main class="flyer">
    <section class="hero" role="img" aria-label="Photo of a smiling student holding a geography book in front of a world map">
      <ul class="headlines">
        <li class="headline">Feeling overwhelmed<br>by the HSC?</li>
        <li class="headline">Looking to improve<br>your skills,confidence<br>and organisation?</li>
        <li class="headline">Want to increase your<br>child’s engagement<br>at school?</li>
      </ul>
    </section>

    <p class="intro">Lumora Tutoring offers one-on-one, individualised learning experiences to maximise academic development. Our tutors are hand selected on the basis of their qualifications, expertise and passion for inspiring young learners.</p>

    <div class="offer">
      <span class="offer-lead">Mention this advertisement to claim</span>
      <span class="offer-deal">Your trial session for just $10!</span>
    </div>

    <p class="call-to-action">Contact us today to discuss how we can help make your learning goals a reality!</p>

    <div class="brand">
      <span class="brand-mark"></span>
      <span class="brand-name">lumora</span>
    </div>

    <footer class="contact-bar">
      <div class="contact-row primary">
        <svg class="icon" viewBox="0 0 14 14"><rect x="1" y="2.5" width="12" height="9" rx="1.5" fill="#fff"/><path d="M2 4 L7 8 L12 4" stroke="#4a9fd8" stroke-width="1.3" fill="none"/></svg>
        <span>info@lumoratutoring.com.au</span>
        <span class="gap"></span>
        <svg class="icon" viewBox="0 0 14 14"><rect x="0.5" y="0.5" width="13" height="13" rx="2" fill="#fff"/><circle cx="7" cy="7" r="4.3" stroke="#4a9fd8" stroke-width="1.1" fill="none"/><path d="M2.7 7 H11.3 M7 2.7 C4.8 5 4.8 9 7 11.3 M7 2.7 C9.2 5 9.2 9 7 11.3" stroke="#4a9fd8" stroke-width="0.9" fill="none"/></svg>
        <span>www.lumoratutoring.com.au</span>
      </div>
      <div class="contact-row address">
        <svg class="icon small" viewBox="0 0 11 11"><rect x="0" y="0" width="11" height="11" rx="1.5" fill="#fff"/><path d="M5.5 2 C3.8 2 3 3.2 3 4.4 C3 6 5.5 9 5.5 9 C5.5 9 8 6 8 4.4 C8 3.2 7.2 2 5.5 2 Z" fill="#4a9fd8"/><circle cx="5.5" cy="4.4" r="1" fill="#fff"/></svg>
        <span>Suite 3, 48 Harlow Street Lindfield, Nsw 2070</span>
      </div>
    </footer>
  </main>
</body>
</html>
```